MRT Property - Business Cards

Looking for a business card & general letterhead, signage etc design for our new logo.

Colours:
000a20
0056a2
00b5ef
0088ce
68cef2

Fonts:
Poppins
Karla

Please keep look and feel of new brand - example in the zip package I sent.

```html
<!DOCTYPE html>
<html lang="en">
<head>
<meta charset="utf-8">
<title>MRT Property – Stationery</title>
<link href="https://fonts.googleapis.com/css2?family=Poppins:wght@400;500;600;700&display=swap" rel="stylesheet">
<style>
  :root {
    --ink: #000a20;
    --royal: #0056a2;
    --cyan: #00b5ef;
    --ocean: #0088ce;
    --sky: #68cef2;
    --paper: #ffffff;
    --backdrop: #e9ecf0;
  }
  * { box-sizing: border-box; margin: 0; padding: 0; }
  html, body { width: 1200px; height: 686px; overflow: hidden; }
  body {
    background: var(--backdrop);
    font-family: "Poppins", sans-serif;
    color: var(--ink);
    position: relative;
  }
  .letterhead {
    position: absolute; left: 70px; top: 30px;
    width: 442px; height: 626px;
    background: var(--paper);
    box-shadow: 0 4px 18px rgba(0,10,32,.12);
    overflow: hidden;
  }
  .swoosh { position: absolute; left: 0; bottom: 0; }
  .wordmark {
    font-weight: 700; color: var(--royal);
    letter-spacing: .5px; white-space: nowrap;
    display: flex; align-items: center; gap: 8px;
  }
  .wordmark .mark-square { width: 12px; height: 12px; background: var(--sky); display: inline-block; }
  .letterhead .wordmark { position: absolute; right: 34px; top: 40px; font-size: 22px; }
  .letterhead .contact {
    position: absolute; right: 34px; top: 96px;
    border-left: 1.5px solid var(--royal);
    padding-left: 14px;
    font-size: 9px; line-height: 1.6;
  }
  .contact-row { display: flex; align-items: center; gap: 6px; }
  .contact-row svg { width: 9px; height: 9px; flex: none; }
  .address { margin-top: 2px; padding-left: 15px; }

  .card {
    position: absolute; width: 360px; height: 206px;
    box-shadow: 0 4px 16px rgba(0,10,32,.14);
    overflow: hidden;
  }
  .card-front { left: 600px; top: 92px; background: var(--paper); }
  .card-back { left: 780px; top: 370px; background: var(--royal); display: flex; align-items: center; justify-content: center; }
  .card-front .wordmark { position: absolute; right: 26px; top: 22px; font-size: 19px; }
  .card-back .wordmark { font-size: 26px; color: var(--sky); }
  .card-back .wordmark .mark-square { width: 14px; height: 14px; }
  .holder { position: absolute; right: 26px; top: 70px; text-align: right; }
  .holder-name { font-size: 17px; font-weight: 600; color: var(--royal); line-height: 1.1; }
  .holder-name .surname { font-weight: 400; color: var(--sky); }
  .holder-role { font-size: 9px; font-weight: 500; }
  .holder-accent { position: absolute; right: 0; top: 74px; width: 12px; height: 26px; background: var(--sky); }
  .card-front .contact { position: absolute; left: 24px; top: 24px; font-size: 8px; line-height: 1.7; }
  .card-front .address-block { position: absolute; right: 26px; bottom: 22px; text-align: right; font-size: 8px; line-height: 1.55; }
</style>
</head>
<body>

  <section class="letterhead">
    <div class="wordmark"><span class="mark-square"></span>MRT Property</div>
    <div class="contact">
      <div class="contact-row"><svg viewBox="0 0 10 10"><path d="M2 1l2 2-1 1.3c.6 1.2 1.5 2.1 2.7 2.7L7 6l2 2-1.3 1.3C4.5 9 1 5.5.7 2.3z" fill="var(--royal)"/></svg>+61 2 9000 1234</div>
      <div class="contact-row"><svg viewBox="0 0 10 10"><circle cx="5" cy="5" r="4" fill="none" stroke="var(--royal)"/><path d="M1 5h8M5 1c2 2.5 2 5.5 0 8M5 1c-2 2.5-2 5.5 0 8" fill="none" stroke="var(--royal)" stroke-width=".7"/></svg>www.mrtproperty.com.au</div>
      <div class="contact-row"><svg viewBox="0 0 10 10"><rect x=".5" y="2" width="9" height="6" fill="none" stroke="var(--royal)"/><path d="M.5 2L5 5.5 9.5 2" fill="none" stroke="var(--royal)"/></svg>info@mrtproperty.com.au</div>
      <div class="contact-row"><svg viewBox="0 0 10 10"><path d="M5 9.5S1.5 5.8 1.5 3.7a3.5 3.5 0 0 1 7 0C8.5 5.8 5 9.5 5 9.5z" fill="var(--royal)"/><circle cx="5" cy="3.7" r="1.2" fill="#fff"/></svg>Suite 4.12, Level 4</div>
      <div class="address">18 Harbour Lane<br>Rivermead NSW 2150</div>
    </div>
    <svg class="swoosh" width="442" height="626" viewBox="0 0 442 626">
      <path d="M0 0 C 60 200 220 470 442 626 L 0 626 Z" fill="var(--sky)" transform="translate(0,120)"/>
      <path d="M0 170 C 70 360 220 520 400 626 L 0 626 Z" fill="#fff"/>
      <path d="M0 200 C 60 380 200 530 360 626 L 0 626 Z" fill="var(--royal)"/>
    </svg>
  </section>

  <section class="card card-front">
    <svg class="swoosh" width="360" height="206" viewBox="0 0 360 206">
      <path d="M0 80 C 80 120 170 160 250 206 L 0 206 Z" fill="var(--sky)"/>
      <path d="M0 100 C 70 130 150 168 220 206 L 0 206 Z" fill="#fff"/>
      <path d="M0 110 C 70 140 140 172 200 206 L 0 206 Z" fill="var(--royal)"/>
    </svg>
    <div class="wordmark"><span class="mark-square"></span>MRT Property</div>
    <div class="contact">
      <div class="contact-row"><svg viewBox="0 0 10 10"><path d="M2 1l2 2-1 1.3c.6 1.2 1.5 2.1 2.7 2.7L7 6l2 2-1.3 1.3C4.5 9 1 5.5.7 2.3z" fill="var(--royal)"/></svg>+61 2 9000 1234</div>
      <div class="contact-row"><svg viewBox="0 0 10 10"><circle cx="5" cy="5" r="4" fill="none" stroke="var(--royal)"/><path d="M1 5h8" stroke="var(--royal)" stroke-width=".7"/></svg>www.mrtproperty.com.au</div>
      <div class="contact-row"><svg viewBox="0 0 10 10"><rect x=".5" y="2" width="9" height="6" fill="none" stroke="var(--royal)"/><path d="M.5 2L5 5.5 9.5 2" fill="none" stroke="var(--royal)"/></svg>info@mrtproperty.com.au</div>
    </div>
    <div class="holder">
      <div class="holder-name">Liam <span class="surname">Porter</span></div>
      <div class="holder-role">Director</div>
    </div>
    <span class="holder-accent"></span>
    <div class="address-block">Suite 4.12, Level 4<br>18 Harbour Lane<br>Rivermead NSW 2150</div>
  </section>

  <section class="card card-back">
    <div class="wordmark"><span class="mark-square"></span>MRT Property</div>
  </section>

</body>
</html>
```